Bramwell Corner Sports Pub. Where the locals go!!

We are creating a sports pub. We are needing a fun website that offers our menu along with an event page and general info. We have some attached links that we really like:
https://www.dunmorrows.example/
https://www.cafepelindra.example/
https://www.quillstoneyx.example/
We are doing a pirate theme but that is because the area we are in. We would like to see a pirate like in our logo doing something like drinking real time similar to the dunmorrows website above.
Target Market(s)
Sports Fans
Industry/Entity Type
Pub, Bar, Restaurant
Coding
Coded - Design and coding required
Number of Pages Required
3 page
Font styles to use
Other font styles liked:
- see uploads
Look and feel

```html
<!DOCTYPE html>
<html lang="en">
<head>
<meta charset="utf-8">
<title>Bramwell Corner Sports Pub</title>
<link href="https://fonts.googleapis.com/css2?family=Rye&family=Staatliches&family=Poppins:wght@400;500;600&display=swap" rel="stylesheet">
<style>
:root{
  --dark:#26292b;
  --dark-2:#2f3133;
  --cream:#efe1c7;
  --field:#f5efe4;
  --red:#d9473b;
  --amber:#f4a21f;
  --ink:#2b2b2b;
  --muted:#5a534a;
  --light:#f2e7d3;
  --line:#44474a;
}
*{box-sizing:border-box;margin:0;padding:0}
html,body{width:1200px;height:3231px;overflow:hidden}
body{position:relative;background:var(--cream);font-family:"Poppins",sans-serif;color:var(--ink)}
.abs{position:absolute}
.display{font-family:"Rye",serif;letter-spacing:3px}
.label{font-family:"Staatliches",sans-serif;letter-spacing:1px}

/* header */
.site-header{left:0;top:0;width:1200px;height:184px;background:var(--dark)}
.phone-badge{left:111px;top:42px;width:43px;height:43px;border-radius:50%;background:var(--amber);display:flex;align-items:center;justify-content:center}
.phone-number{left:170px;top:50px;font-family:"Staatliches",sans-serif;font-size:22px;color:var(--light);letter-spacing:2px}
.brand{left:450px;top:38px;width:300px;text-align:center;font-family:"Poppins",sans-serif;font-weight:600;font-size:20px;line-height:26px;color:var(--red)}
.socials{display:flex;gap:8px}
.social{width:35px;height:35px;border-radius:50%;background:#1d1f21;border:1px solid #3a3d40}
.header-socials{left:922px;top:46px}
.main-nav{left:0;top:127px;width:1200px;height:57px;border-top:1px solid var(--line);border-bottom:1px solid var(--line);display:flex;justify-content:center}
.main-nav a{font-family:"Staatliches",sans-serif;font-size:19px;color:var(--light);text-decoration:none;line-height:55px;padding:0 33px;border-left:1px solid var(--line);letter-spacing:1px}
.main-nav a:last-child{border-right:1px solid var(--line)}
.main-nav a.active{color:var(--amber)}

/* hero */
.hero{left:0;top:184px;width:1200px;height:630px;background:radial-gradient(ellipse at 55% 45%,#c98a25 0%,#7a4a18 28%,#3a2a1f 55%,#222426 85%)}
.hero-title{left:0;top:690px;width:1200px;text-align:center;font-size:52px;color:var(--light);text-shadow:0 3px 0 #8a7256}
.btn{display:inline-block;font-family:"Staatliches",sans-serif;font-size:21px;letter-spacing:1px;color:#fff;text-align:center;border-radius:3px}
.btn-red{background:var(--red)}
.btn-amber{background:var(--amber)}

/* story */
.photo{border:6px solid #fbf7ef;box-shadow:0 2px 8px rgba(0,0,0,.2)}
.section-title{font-size:42px;color:var(--ink)}
.body-text{font-size:15.5px;line-height:25.5px;color:var(--muted);text-align:justify}

/* menus */
.menus{left:0;top:1818px;width:1200px;height:628px;background:radial-gradient(ellipse at 50% 30%,#4a3b30 0%,#2e2a28 50%,#232527 100%)}
.menu-card{top:1986px;width:253px;height:319px;border:2px solid var(--light);text-align:center}
.menu-card.featured{border-color:var(--red)}
.menu-thumb{position:absolute;left:69px;top:26px;width:112px;height:112px;border-radius:50%;border:3px solid var(--light);background:radial-gradient(circle,#c98a2a,#5a3a20)}
.menu-name{position:absolute;left:0;top:166px;width:100%;font-family:"Staatliches",sans-serif;font-size:22px;color:var(--light);letter-spacing:1px}
.menu-desc{position:absolute;left:20px;top:202px;width:209px;font-size:14px;line-height:25px;color:var(--light)}
.menu-go{position:absolute;left:107px;top:299px;width:36px;height:36px;border-radius:50%;background:var(--light);display:flex;align-items:center;justify-content:center}
.featured .menu-go{background:var(--red)}
.dot{top:2367px;width:10px;height:10px;border-radius:50%;background:#7b7570}

/* signup */
.field{top:2703px;height:52px;background:var(--field);border-radius:3px;box-shadow:0 1px 4px rgba(0,0,0,.12);font-size:16px;color:#6a6258;padding:15px 18px}

/* footer */
.site-footer{left:0;top:2866px;width:1200px;height:365px;background:var(--dark)}
.foot-title{font-family:"Staatliches",sans-serif;font-size:22px;color:var(--light);letter-spacing:1px}
.foot-list{list-style:none;font-size:15px;color:var(--light)}
.foot-list li{display:flex;gap:14px;align-items:flex-start}
.foot-list strong{font-weight:500;display:block;font-size:14.5px}
.foot-list span{font-size:13px;line-height:22px}
</style>
</head>
<body>

<header class="abs site-header">
  <div class="abs phone-badge">
    <svg width="20" height="20" viewBox="0 0 24 24"><path fill="#26292b" d="M6.6 10.8a15 15 0 0 0 6.6 6.6l2.2-2.2c.3-.3.7-.4 1-.2 1.1.4 2.3.6 3.6.6.6 0 1 .4 1 1V20c0 .6-.4 1-1 1A17 17 0 0 1 3 4c0-.6.4-1 1-1h3.5c.6 0 1 .4 1 1 0 1.3.2 2.5.6 3.6.1.3 0 .7-.2 1z"/></svg>
  </div>
  <div class="abs phone-number">+1 (555) 014 2288</div>
  <div class="abs brand">Bramwell Corner<br>Sports Pub</div>
  <div class="abs socials header-socials">
    <span class="social"></span><span class="social"></span><span class="social"></span><span class="social"></span>
  </div>
  <nav class="abs main-nav">
    <a class="active">Home</a><a>Our Story</a><a>Our Menu</a><a>Events</a><a>Contact Us</a>
  </nav>
</header>

<section>
  <div class="abs hero" role="img" aria-label="Two glasses of beer clinking in a dim pub"></div>
  <h1 class="abs display hero-title">BRAMWELL CORNER SPORTS PUB</h1>
  <a class="abs btn btn-red" style="left:441px;top:789px;width:154px;line-height:50px">Reservation</a>
  <a class="abs btn btn-amber" style="left:605px;top:789px;width:154px;line-height:50px">Contact Us</a>
</section>

<section>
  <h2 class="abs display section-title" style="left:111px;top:1005px">OUR STORY</h2>
  <p class="abs body-text" style="left:111px;top:1080px;width:358px">Lorem ipsum dolor sit amet, consectetur adipis cing elit, sed do eiusmod tempor incididunt ut labore et dolore magna aliqua. Ut enim ad minim veniam, quis nostrud exercitation ullamco labo ris nisi ut aliquip ex ea commodo consequat. Duis aute irure dolor in reprehe.</p>
  <div class="abs photo" style="left:530px;top:960px;width:558px;height:326px;background:linear-gradient(135deg,#3a2a20,#b9722e 55%,#5a3a22)" role="img" aria-label="Long wooden bar counter with beer taps and screens"></div>
  <div class="abs photo" style="left:111px;top:1342px;width:398px;height:342px;background:linear-gradient(160deg,#7a1f18,#c25a2a 45%,#3a2018)" role="img" aria-label="Crowded pub interior with guests at the bar"></div>
  <p class="abs body-text" style="left:582px;top:1376px;width:506px">Lorem ipsum dolor sit amet, consectetur adipis cing elit, sed do eiusmod tempor incididunt ut labore et dolore magna aliqua. Ut enim ad minim veniam, quis nostrud exercitation ullamco labo ris nisi ut aliquip ex ea commodo consequat. Duis aute irure dolor in reprehe. nderit in voluptate velit esse cillum dolore eu fugiat nulla pariatur. Excepteur sint occaecat cupidatat non proident, sunt in culpa qui officia deserunt mollit anim id est laborum.</p>
  <a class="abs btn btn-red" style="left:582px;top:1590px;width:146px;line-height:52px">Learn More</a>
</section>

<section>
  <div class="abs menus" role="img" aria-label="Blurred crowd of fans cheering in the pub"></div>
  <h2 class="abs display section-title" style="left:0;top:1875px;width:1200px;text-align:center;color:var(--light)">OUR SPECIAL MENUS</h2>
  <div class="abs menu-card" style="left:43px"><div class="menu-thumb" role="img" aria-label="Beer glasses"></div><div class="menu-name">Lorem Ipsum Dol</div><p class="menu-desc">Lorem ipsum dolor sit amet, consectetur adipis cing elit, sed do eiusm.</p><div class="menu-go"><svg width="14" height="14" viewBox="0 0 14 14"><path d="M5 2l5 5-5 5" fill="none" stroke="#26292b" stroke-width="2"/></svg></div></div>
  <div class="abs menu-card" style="left:330px"><div class="menu-thumb" role="img" aria-label="Beer tasting flight"></div><div class="menu-name">Lorem Ipsum Dol</div><p class="menu-desc">Lorem ipsum dolor sit amet, consectetur adipis cing elit, sed do eiusm.</p><div class="menu-go"><svg width="14" height="14" viewBox="0 0 14 14"><path d="M5 2l5 5-5 5" fill="none" stroke="#26292b" stroke-width="2"/></svg></div></div>
  <div class="abs menu-card featured" style="left:617px"><div class="menu-thumb" role="img" aria-label="Guests toasting"></div><div class="menu-name">Lorem Ipsum Dol</div><p class="menu-desc">Lorem ipsum dolor sit amet, consectetur adipis cing elit, sed do eiusm.</p><div class="menu-go"><svg width="14" height="14" viewBox="0 0 14 14"><path d="M5 2l5 5-5 5" fill="none" stroke="#fff" stroke-width="2"/></svg></div></div>
  <div class="abs menu-card" style="left:903px"><div class="menu-thumb" role="img" aria-label="Bartender pouring beer"></div><div class="menu-name">Lorem Ipsum Dol</div><p class="menu-desc">Lorem ipsum dolor sit amet, consectetur adipis cing elit, sed do eiusm.</p><div class="menu-go"><svg width="14" height="14" viewBox="0 0 14 14"><path d="M5 2l5 5-5 5" fill="none" stroke="#26292b" stroke-width="2"/></svg></div></div>
  <span class="abs dot" style="left:565px"></span><span class="abs dot" style="left:585px;background:var(--amber)"></span><span class="abs dot" style="left:605px"></span><span class="abs dot" style="left:625px"></span>
</section>

<section>
  <h2 class="abs display section-title" style="left:0;top:2550px;width:1200px;text-align:center">SIGN UP FOR UPDATES</h2>
  <p class="abs" style="left:210px;top:2617px;width:780px;text-align:center;font-size:15.5px;line-height:26px;color:var(--muted)">Lorem ipsum dolor sit amet, consectetur adipis cing elit, sed do eiusmod tempor incididunt ut labore et dolore magna minim quis nostrud exercitation ulla.</p>
  <div class="abs field" style="left:163px;width:351px">Name</div>
  <div class="abs field" style="left:526px;width:351px">Email Address</div>
  <a class="abs btn btn-red" style="left:900px;top:2703px;width:137px;line-height:52px">Sign Up</a>
</section>

<footer class="abs site-footer">
  <div class="abs" style="left:111px;top:100px;width:222px;text-align:center;font-weight:600;font-size:22px;line-height:30px;color:var(--red)">Bramwell Corner<br>Sports Pub</div>

  <h3 class="abs foot-title" style="left:421px;top:62px">Quick Links</h3>
  <ul class="abs foot-list" style="left:421px;top:112px;line-height:34.5px">
    <li><svg width="13" height="13" viewBox="0 0 14 14" style="margin-top:11px"><circle cx="7" cy="7" r="6.5" fill="var(--amber)"/><path d="M5.5 4l3 3-3 3" fill="none" stroke="#26292b" stroke-width="1.6"/></svg>Home</li>
    <li><svg width="13" height="13" viewBox="0 0 14 14" style="margin-top:11px"><circle cx="7" cy="7" r="6.5" fill="var(--amber)"/><path d="M5.5 4l3 3-3 3" fill="none" stroke="#26292b" stroke-width="1.6"/></svg>Our Story</li>
    <li><svg width="13" height="13" viewBox="0 0 14 14" style="margin-top:11px"><circle cx="7" cy="7" r="6.5" fill="var(--amber)"/><path d="M5.5 4l3 3-3 3" fill="none" stroke="#26292b" stroke-width="1.6"/></svg>Our Menu</li>
    <li><svg width="13" height="13" viewBox="0 0 14 14" style="margin-top:11px"><circle cx="7" cy="7" r="6.5" fill="var(--amber)"/><path d="M5.5 4l3 3-3 3" fill="none" stroke="#26292b" stroke-width="1.6"/></svg>Events</li>
    <li><svg width="13" height="13" viewBox="0 0 14 14" style="margin-top:11px"><circle cx="7" cy="7" r="6.5" fill="var(--amber)"/><path d="M5.5 4l3 3-3 3" fill="none" stroke="#26292b" stroke-width="1.6"/></svg>Contact Us</li>
  </ul>

  <h3 class="abs foot-title" style="left:643px;top:62px">Contact</h3>
  <ul class="abs foot-list" style="left:643px;top:114px;width:240px">
    <li style="height:66px"><svg width="12" height="14" viewBox="0 0 12 16" style="margin-top:4px"><path d="M6 0a6 6 0 0 0-6 6c0 4.5 6 10 6 10s6-5.5 6-10a6 6 0 0 0-6-6zm0 8.5A2.5 2.5 0 1 1 6 3.5a2.5 2.5 0 0 1 0 5z" fill="var(--amber)"/></svg><div><strong>ADDRESS:</strong><span>465, Lorum Ipsum Dolore Sed, United States</span></div></li>
    <li style="height:58px"><svg width="13" height="13" viewBox="0 0 24 24" style="margin-top:4px"><path fill="var(--amber)" d="M6.6 10.8a15 15 0 0 0 6.6 6.6l2.2-2.2c.3-.3.7-.4 1-.2 1.1.4 2.3.6 3.6.6.6 0 1 .4 1 1V20c0 .6-.4 1-1 1A17 17 0 0 1 3 4c0-.6.4-1 1-1h3.5c.6 0 1 .4 1 1 0 1.3.2 2.5.6 3.6.1.3 0 .7-.2 1z"/></svg><div><strong>PHONE:</strong><span>+1 (555) 014 2288</span></div></li>
    <li><svg width="14" height="11" viewBox="0 0 16 12" style="margin-top:5px"><rect width="16" height="12" rx="1" fill="var(--amber)"/><path d="M0 1l8 6 8-6" fill="none" stroke="#26292b" stroke-width="1.3"/></svg><div><strong>EMAIL:</strong><span>info@bramwellcorner.example</span></div></li>
  </ul>

  <h3 class="abs foot-title" style="left:943px;top:62px">Working Hours</h3>
  <ul class="abs foot-list" style="left:943px;top:114px;width:160px">
    <li style="height:58px"><svg width="13" height="13" viewBox="0 0 14 14" style="margin-top:4px"><circle cx="7" cy="7" r="6" fill="none" stroke="var(--amber)" stroke-width="1.6"/><path d="M7 3.5V7l2.5 1.5" fill="none" stroke="var(--amber)" stroke-width="1.6"/></svg><div><strong>FRIDAY:</strong><span>11am to 10pm</span></div></li>
    <li style="height:58px"><svg width="13" height="13" viewBox="0 0 14 14" style="margin-top:4px"><circle cx="7" cy="7" r="6" fill="none" stroke="var(--amber)" stroke-width="1.6"/><path d="M7 3.5V7l2.5 1.5" fill="none" stroke="var(--amber)" stroke-width="1.6"/></svg><div><strong>SATURDAY:</strong><span>11am to 10pm</span></div></li>
    <li><svg width="13" height="13" viewBox="0 0 14 14" style="margin-top:4px"><circle cx="7" cy="7" r="6" fill="none" stroke="var(--amber)" stroke-width="1.6"/><path d="M7 3.5V7l2.5 1.5" fill="none" stroke="var(--amber)" stroke-width="1.6"/></svg><div><strong>SUNDAY:</strong><span>11am to 10pm</span></div></li>
  </ul>

  <div class="abs" style="left:111px;top:299px;width:978px;height:1px;background:var(--line)"></div>
  <p class="abs" style="left:0;top:317px;width:1200px;text-align:center;font-size:13px;color:var(--light)">© 2023 Bramwell Corner Sports Pub &nbsp;|&nbsp; All Rights Reserved</p>
  <div class="abs socials" style="left:922px;top:310px">
    <span class="social"></span><span class="social"></span><span class="social"></span><span class="social"></span>
  </div>
</footer>

</body>
</html>
```